Verdo Consultants Exhibition Booth Design. Cannabis Legal Consultancy

We require a design for the following artwork in PDF of Jpeg high resolution format with these specifications, a 5cm bleed outside and a 10cm safe inside bleed. A tension fabric backdrop 200cm wide and 231cm high. (example loaded) Please see our website www.theverdoconsultants.co.uk
Attached are company logos and head shots for inclusion. You will see our colour schemes from the website. It should announce who we are and provide the company website.

```html
<!DOCTYPE html>
<html lang="en">
<head>
<meta charset="utf-8">
<title>Verdo Consultants – Exhibition Backdrop</title>
<link href="https://fonts.googleapis.com/css2?family=Bebas+Neue&family=Montserrat:wght@400;500&display=swap" rel="stylesheet">
<style>
  :root {
    --brand-blue: #1652f0;
    --ink-dark: #3d4347;
    --paper: #ffffff;
    --stage: #e3e8e8;
    --photo-deep: #1f2427;
    --photo-mid: #6d7a7e;
    --portrait-light: #c9ccce;
    --portrait-dark: #2e3235;
  }
  * { margin: 0; padding: 0; box-sizing: border-box; }
  html, body {
    width: 1200px; height: 977px; overflow: hidden;
    background: var(--stage);
  }
  .backdrop {
    position: absolute; left: 210px; top: 38px;
    width: 779px; height: 900px;
    background: var(--paper);
    overflow: hidden;
    box-shadow: 0 10px 30px rgba(0,0,0,0.12);
  }
  .backdrop__art { position: absolute; inset: 0; }
  .brand {
    position: absolute; left: 451px; top: 48px;
    display: flex; align-items: center; gap: 12px;
  }
  .brand__mark {
    width: 88px; height: 88px; border-radius: 50%;
    border: 4px solid var(--brand-blue);
    flex: none;
  }
  .brand__text {
    font-family: "Montserrat", sans-serif; font-weight: 500;
    color: var(--brand-blue); line-height: 1.02;
  }
  .brand__name { font-size: 24px; letter-spacing: 0.3px; }
  .brand__url {
    font-family: "Montserrat", sans-serif; font-weight: 400;
    font-size: 9.5px; color: var(--ink-dark); margin-top: 4px;
  }
  .services {
    position: absolute; right: 28px; top: 188px;
    text-align: right;
    font-family: "Bebas Neue", sans-serif; font-weight: 400;
    color: var(--brand-blue);
    font-size: 74px; line-height: 78px;
    transform: scaleX(0.82); transform-origin: right top;
  }
  .name-tag {
    position: absolute;
    background: var(--brand-blue); color: var(--paper);
    font-family: "Bebas Neue", sans-serif; font-size: 30px;
    line-height: 46px; height: 46px; padding: 0 24px;
    border-radius: 18px; white-space: nowrap;
  }
  .name-tag--left { left: 100px; top: 822px; }
  .name-tag--right { left: 380px; top: 702px; }
  .site {
    position: absolute; right: 28px; top: 812px;
    font-family: "Montserrat", sans-serif; font-weight: 500;
    font-size: 23px; color: var(--ink-dark);
  }
  .site__rule {
    position: absolute; right: 28px; top: 850px;
    width: 330px; height: 2px; background: var(--ink-dark);
  }
  .site__rule::before {
    content: ""; position: absolute; left: -4px; top: -4px;
    width: 10px; height: 10px; border-radius: 50%; background: var(--ink-dark);
  }
</style>
</head>
<body>
  <main class="backdrop">
    <svg class="backdrop__art" width="779" height="900" viewBox="0 0 779 900">
      <defs>
        <radialGradient id="compass-tone" cx="0.45" cy="0.4" r="0.7">
          <stop offset="0" stop-color="#6d7a7e"/>
          <stop offset="1" stop-color="#1f2427"/>
        </radialGradient>
        <linearGradient id="portrait-tone" x1="0" y1="0" x2="0" y2="1">
          <stop offset="0" stop-color="#c9ccce"/>
          <stop offset="1" stop-color="#2e3235"/>
        </linearGradient>
      </defs>

      <!-- feature image rings -->
      <path class="ring ring--outer" d="M 136 15 A 310 310 0 0 1 497 360" fill="none" stroke="var(--ink-dark)" stroke-width="6"/>
      <path class="ring ring--outer" d="M 474 445 A 310 310 0 0 1 442 500" fill="none" stroke="var(--ink-dark)" stroke-width="6"/>
      <path class="ring ring--blue" d="M -21 172 A 258 258 0 0 1 413 191" fill="none" stroke="var(--brand-blue)" stroke-width="12"/>
      <path class="ring ring--blue" d="M -52 408 A 258 258 0 0 0 278 562" fill="none" stroke="var(--brand-blue)" stroke-width="12"/>
      <path class="ring ring--dark" d="M -82 447 A 300 300 0 0 0 340 580" fill="none" stroke="var(--ink-dark)" stroke-width="14"/>
      <circle class="ring ring--dark" cx="190" cy="320" r="218" fill="none" stroke="var(--ink-dark)" stroke-width="14"/>
      <circle class="feature-photo" cx="190" cy="320" r="205" fill="url(#compass-tone)"
              role="img" aria-label="Close-up photograph of a compass needle pointing towards the word answers"/>

      <!-- left portrait -->
      <circle cx="205" cy="670" r="140" fill="var(--paper)" stroke="var(--ink-dark)" stroke-width="5"/>
      <circle cx="205" cy="670" r="124" fill="var(--paper)" stroke="var(--brand-blue)" stroke-width="5"/>
      <circle cx="205" cy="670" r="106" fill="none" stroke="var(--ink-dark)" stroke-width="5"/>
      <circle class="portrait" cx="205" cy="670" r="102" fill="url(#portrait-tone)"
              role="img" aria-label="Headshot portrait of Daniel Hart"/>

      <!-- right portrait -->
      <circle cx="462" cy="570" r="118" fill="var(--paper)" stroke="var(--ink-dark)" stroke-width="5"/>
      <circle cx="462" cy="570" r="103" fill="var(--paper)" stroke="var(--brand-blue)" stroke-width="5"/>
      <circle cx="462" cy="570" r="88" fill="none" stroke="var(--ink-dark)" stroke-width="5"/>
      <circle class="portrait" cx="462" cy="570" r="84" fill="url(#portrait-tone)"
              role="img" aria-label="Headshot portrait of Owen Fletcher"/>
    </svg>

    <div class="brand">
      <span class="brand__mark"></span>
      <div class="brand__text">
        <div class="brand__name">THE<br>VERDO<br>CONSULTANTS</div>
        <div class="brand__url">www.theverdoconsultants.co.uk</div>
      </div>
    </div>

    <h1 class="services">ASSESSMENT<br>ADVICE<br>IMPLEMENTATION</h1>

    <div class="name-tag name-tag--right">OWEN FLETCHER</div>
    <div class="name-tag name-tag--left">DANIEL HART</div>

    <p class="site">theverdoconsultants.co.uk</p>
    <div class="site__rule"></div>
  </main>
</body>
</html>
```